Business card for builder specialising in renovations.

Need a card for our building business. Business name is under Martin Powles.
Have licence number on card ( 527691K)
Contact number (0400 382 415)
Want to work on logo for some business cards and shirts - something with MP or MPB or open to ideas??
No animations, No hammers. Something sharp and eye catching.
Highlight that we are a renovation specialist. Simple on front with extra details on back with some lines to jot down things.

Target Market(s)

Renovators

Industry/Entity Type

Building

Contact Information for Business Card

2 sided with room on back to jot things down.
Extra details on back so front can be simple ..like, renovations, bathrooms, decks, extensions, new builds,

Logo Text

MP

Font styles to use
Serif

Requirements
Must have
• Eye catching design .
• Name : Martin powles
• Licence number
• Contact number - 0400382415
Nice to have
• Some logo design that we can carry through to other forms of advertising
• Local builder
• Quality work
Should not have
• No animations

```html
<!DOCTYPE html>
<html lang="en">
<head>
<meta charset="utf-8">
<title>Martin Powles – Business Card</title>
<link href="https://fonts.googleapis.com/css2?family=Libre+Baskerville:wght@400;700&display=swap" rel="stylesheet">
<style>
  :root {
    --page: #2b2b2b;
    --ink: #0a0a0a;
    --paper: #ffffff;
    --blue: #1a73c4;
    --grey: #d9dde2;
    --serif: "Libre Baskerville", "Times New Roman", serif;
  }
  * { margin: 0; padding: 0; box-sizing: border-box; }
  html, body { width: 1200px; height: 900px; overflow: hidden; }
  body { background: var(--page); font-family: var(--serif); position: relative; }

  .card {
    position: absolute;
    width: 700px;
    height: 400px;
    border-radius: 22px;
    overflow: hidden;
    box-shadow: 0 14px 30px rgba(0,0,0,.45);
  }

  /* ---------- Front ---------- */
  .card--front { left: 70px; top: 40px; background: var(--ink); color: var(--paper); }
  .front__brand {
    position: absolute; left: 0; right: 0; top: 120px;
    display: flex; justify-content: center; align-items: center; gap: 16px;
  }
  .brand-mark { width: 22px; height: 22px; background: var(--blue); }
  .front__name { font-size: 46px; font-weight: 400; letter-spacing: 2px; color: var(--paper); }
  .front__services {
    position: absolute; left: 0; right: 0; top: 232px;
    text-align: center; font-size: 17px; letter-spacing: 1px;
  }
  .front__services .dot {
    display: inline-block; width: 9px; height: 9px; background: var(--blue);
    margin: 0 12px; vertical-align: middle;
  }
  .front__band {
    position: absolute; left: 0; bottom: 0; width: 330px; height: 78px;
    background: var(--blue);
    clip-path: polygon(0 0, 88% 0, 100% 100%, 0 100%);
  }
  .front__strip {
    position: absolute; right: 0; bottom: 0; width: 400px; height: 24px;
    background: var(--paper);
    clip-path: polygon(6% 0, 100% 0, 100% 100%, 0 100%);
  }
  .front__web {
    position: absolute; left: 42px; bottom: 24px;
    font-size: 19px; color: var(--paper); letter-spacing: .5px;
  }

  /* ---------- Back ---------- */
  .card--back { left: 430px; top: 470px; background: var(--paper); color: var(--ink); }
  .back__brand {
    position: absolute; left: 40px; top: 58px;
    display: flex; align-items: center; gap: 12px;
  }
  .back__brand .brand-mark { width: 18px; height: 18px; }
  .back__brandname { font-size: 32px; letter-spacing: 1.5px; color: var(--ink); }

  .back__person { position: absolute; right: 40px; top: 150px; text-align: right; }
  .back__person-name { font-size: 24px; color: var(--blue); letter-spacing: 1px; }
  .back__person-role { font-size: 13px; color: var(--ink); margin-top: 4px; }

  .back__rule {
    position: absolute; left: 190px; right: 150px; top: 188px;
    height: 2px; background: var(--blue);
  }
  .back__rule--low { left: 40px; right: 330px; top: 290px; }

  .back__contacts { position: absolute; left: 44px; top: 302px; list-style: none; }
  .back__contacts li {
    display: flex; align-items: center; gap: 12px;
    font-size: 17px; line-height: 26px;
  }
  .back__contacts svg { width: 14px; height: 14px; fill: var(--blue); flex: none; }
  .back__contacts .accent { color: var(--blue); }

  .back__shade {
    position: absolute; right: 0; bottom: 0; width: 300px; height: 140px;
    background: var(--ink);
    clip-path: polygon(6% 38%, 100% 38%, 100% 100%, 0 100%);
  }
  .back__band {
    position: absolute; right: 0; bottom: 60px; width: 300px; height: 110px;
    background: var(--blue);
    clip-path: polygon(12% 30%, 100% 0, 100% 100%, 0 100%);
    color: var(--paper);
  }
  .back__licence {
    position: absolute; right: 26px; top: 44px; font-size: 15px; color: var(--paper);
  }
</style>
</head>
<body>

  <section class="card card--front" aria-label="Card front">
    <div class="front__brand">
      <span class="brand-mark"></span>
      <span class="front__name">MARTIN POWLES</span>
    </div>
    <p class="front__services">
      RENOVATIONS<span class="dot"></span>BATHROOMS DECKS<span class="dot"></span>EXTENSIONS<span class="dot"></span>NEW BUILDS
    </p>
    <div class="front__strip"></div>
    <div class="front__band"></div>
    <p class="front__web">www.martinpowles.com</p>
  </section>

  <section class="card card--back" aria-label="Card back">
    <div class="back__brand">
      <span class="brand-mark"></span>
      <span class="back__brandname">MARTIN POWLES</span>
    </div>

    <div class="back__person">
      <p class="back__person-name">MARTIN POWLES</p>
      <p class="back__person-role">Director</p>
    </div>
    <div class="back__rule"></div>
    <div class="back__rule back__rule--low"></div>

    <ul class="back__contacts">
      <li>
        <svg viewBox="0 0 24 24" aria-hidden="true"><path d="M6.6 10.8a15.1 15.1 0 0 0 6.6 6.6l2.2-2.2a1 1 0 0 1 1-.25 11.4 11.4 0 0 0 3.6.57 1 1 0 0 1 1 1V20a1 1 0 0 1-1 1A17 17 0 0 1 3 4a1 1 0 0 1 1-1h3.5a1 1 0 0 1 1 1c0 1.25.2 2.45.57 3.57a1 1 0 0 1-.25 1z"/></svg>
        0400382415
      </li>
      <li>
        <svg viewBox="0 0 24 24" aria-hidden="true"><path d="M2 5h20v14H2zm2 2v.5l8 5 8-5V7zm0 2.8V17h16V9.8l-8 5z"/></svg>
        info@martinpowles.com
      </li>
      <li>
        <svg viewBox="0 0 24 24" aria-hidden="true"><path d="M12 2a10 10 0 1 0 0 20 10 10 0 0 0 0-20zm6.9 6h-3a15.6 15.6 0 0 0-1.3-3.9A8 8 0 0 1 18.9 8zM12 4c.9 1.2 1.6 2.5 2 4h-4c.4-1.5 1.1-2.8 2-4zM4.3 14a8 8 0 0 1 0-4h3.4a16 16 0 0 0 0 4zm.8 2h3a15.6 15.6 0 0 0 1.3 3.9A8 8 0 0 1 5.1 16zm3-8h-3a8 8 0 0 1 4.3-3.9A15.6 15.6 0 0 0 8.1 8zM12 20c-.9-1.2-1.6-2.5-2-4h4c-.4 1.5-1.1 2.8-2 4zm2.3-6H9.7a14 14 0 0 1 0-4h4.6a14 14 0 0 1 0 4zm.3 5.9a15.6 15.6 0 0 0 1.3-3.9h3a8 8 0 0 1-4.3 3.9zM16.3 14a16 16 0 0 0 0-4h3.4a8 8 0 0 1 0 4z"/></svg>
        <span>www.<span class="accent">martinpowles</span>.com</span>
      </li>
    </ul>

    <div class="back__shade"></div>
    <div class="back__band">
      <p class="back__licence">Licence: (527691K)</p>
    </div>
  </section>

</body>
</html>
```